Business Card Design Project

We have recently completed CraftHive projects for a new logo and wesbite.
We now require new business cards.
We hand out very little printed material to clients as all information is online. When we do hand out something, like a business card, we want it to have real impact and make a statement about the quality and professionalism of our company.
We have an idea of what we want our card to look like but we want a designer to make sure they have impact and look great.
Our requirements are…
Size: 85mm X 55mm - Landscape
Front of card: Logo plus the following contact information.
Dennis Marlow
Operations Manager
Phone +44(0) 1632 xxx xxx
Mobile +44(0) 7700 xxx xxx
Email denmo@korvantix.example
Address 17 Pellick Row, Aberdeen AB12 9QZ
Website www.korvantix.example
How you layout the front of the card is up to you, we would like to see some different ideas. Attached are two versions of our logo that may be used.
Back of card: We would like this to be simple but again have impact. Our current thought is to have the logo or just the large W design from the logo in white against a dark background, perhaps made up from the dark green in the logo.
The logos are attached so you can see the colours in them but the dark ones are..
Dark Blue = C:88, M:55, Y:44, K:28
Dark Green = C:87, M:53, Y:50, K:50
We sometimes also use a bright orange as an accent or highlight colour…
Orange: = C:0, M:39, Y:94, K:0

```html
<!DOCTYPE html>
<html lang="en">
<head>
<meta charset="utf-8">
<title>Korvantix Technologies – Business Cards</title>
<link rel="stylesheet" href="https://fonts.googleapis.com/css2?family=Source+Sans+3:wght@400;600;700&display=swap">
<style>
  :root {
    --stage: #e9e7e3;
    --paper: #ffffff;
    --teal-dark: #21434a;
    --teal-text: #2a4b53;
    --olive: #819364;
    --orange: #f9a825;
    --ink: #333a3c;
    --rule: #9aa3a5;
  }
  * { box-sizing: border-box; margin: 0; padding: 0; }
  html, body {
    width: 1200px; height: 800px; overflow: hidden;
    background: var(--stage);
    font-family: "Source Sans 3", Arial, sans-serif;
  }
  .stage { position: relative; width: 1200px; height: 800px; }
  .card {
    position: absolute; width: 502px; height: 325px;
    box-shadow: 0 4px 12px rgba(0,0,0,.25);
    overflow: hidden;
  }
  .card--front { left: 87px; top: 63px; background: var(--paper); }
  .card--back-dark { left: 610px; top: 68px; background: var(--teal-dark); }
  .card--back-gradient { left: 86px; top: 408px;
    background: linear-gradient(135deg, var(--teal-dark) 0%, #4f6a55 45%, var(--olive) 80%); }
  .card--back-light { left: 610px; top: 408px; background: var(--paper); }

  /* Front */
  .brand {
    position: absolute; left: 0; right: 0; top: 66px;
    display: flex; align-items: center; justify-content: center; gap: 10px;
    font-weight: 700; font-size: 30px; letter-spacing: 1px;
    color: var(--teal-text);
  }
  .brand__dot { width: 16px; height: 16px; border-radius: 50%; background: var(--teal-text); }
  .name-band {
    position: absolute; left: 0; right: 0; top: 179px; height: 32px;
    background: var(--orange);
    display: flex; align-items: center; justify-content: center;
    color: var(--teal-text); font-size: 14px;
  }
  .name-band__name { font-weight: 700; font-size: 16px; margin-right: 5px; }
  .address {
    position: absolute; right: 269px; top: 245px;
    text-align: right; font-size: 13.5px; line-height: 19px; color: var(--ink);
  }
  .divider { position: absolute; left: 249px; top: 234px; width: 1px; height: 71px; background: var(--rule); }
  .contacts {
    position: absolute; left: 261px; top: 231px; list-style: none;
    font-size: 13.5px; line-height: 19px; color: var(--ink);
  }
  .contacts li { display: flex; align-items: center; gap: 6px; }
  .contacts svg { width: 10px; height: 10px; fill: var(--ink); }

  /* Backs */
  .wordmark {
    position: absolute; left: 0; right: 0; top: 118px;
    text-align: center; font-weight: 700; font-size: 44px; letter-spacing: 3px;
  }
  .url {
    position: absolute; left: 0; right: 0; top: 265px;
    text-align: center; font-size: 16px; letter-spacing: 3px;
  }
  .card--back-dark .wordmark, .card--back-dark .url,
  .card--back-gradient .wordmark, .card--back-gradient .url { color: #fff; }
  .card--back-light .wordmark, .card--back-light .url { color: var(--teal-text); }
  .card--back-gradient .url { top: 267px; }
  .card--back-light .url { top: 267px; }
</style>
</head>
<body>
<main class="stage">

  <section class="card card--front" aria-label="Card front">
    <div class="brand"><span class="brand__dot"></span>KORVANTIX</div>
    <div class="name-band"><span class="name-band__name">DENNIS MARLOW,</span> Operations Manager</div>
    <address class="address" style="font-style:normal">17 Pellick Row<br>Aberdeen AB12 9QZ</address>
    <div class="divider"></div>
    <ul class="contacts">
      <li><svg viewBox="0 0 10 10"><path d="M2 0.5l2 2-1 1.2c.6 1.3 1.6 2.3 2.9 2.9l1.2-1 2 2-1.2 1.6C4 9 1 6 .4 1.7z"/></svg>+44(0) 1632 xxx xxx</li>
      <li><svg viewBox="0 0 10 10"><path d="M3 0h4a1 1 0 011 1v8a1 1 0 01-1 1H3a1 1 0 01-1-1V1a1 1 0 011-1zm0 1.5v6h4v-6z"/></svg>+44(0) 7700 xxx xxx</li>
      <li><svg viewBox="0 0 10 10"><path d="M0 2h10v6H0zm1 1l4 3 4-3z"/></svg>denmo@korvantix.example</li>
      <li><svg viewBox="0 0 10 10"><path d="M5 0a5 5 0 100 10A5 5 0 005 0zm-3.9 4.5h2a8 8 0 01.6-3A4 4 0 001.1 4.5zm0 1a4 4 0 002.6 3 8 8 0 01-.6-3zm3 0c.1 1.4.5 2.6.9 3.3.4-.7.8-1.9.9-3.3zm0-1h1.8C5.8 3.1 5.4 1.9 5 1.2c-.4.7-.8 1.9-.9 3.3zm2.8 0h2a4 4 0 00-2.6-3 8 8 0 01.6 3zm0 1a8 8 0 01-.6 3 4 4 0 002.6-3z"/></svg>www.korvantix.example</li>
    </ul>
  </section>

  <section class="card card--back-dark" aria-label="Card back, dark">
    <div class="wordmark">KORVANTIX</div>
    <div class="url">www.korvantix.example</div>
  </section>

  <section class="card card--back-gradient" aria-label="Card back, gradient">
    <div class="wordmark">KORVANTIX</div>
    <div class="url">www.korvantix.example</div>
  </section>

  <section class="card card--back-light" aria-label="Card back, light">
    <div class="wordmark">KORVANTIX</div>
    <div class="url">www.korvantix.example</div>
  </section>

</main>
</body>
</html>
```